Brindle Sky Port needs a new upscale business card design for our high end aircraft hangar complex

Brindle Sky Port (BSP) is a large, upscale jet hangar complex in the US housing expensive aircraft. We need a new business card design, using our current logo. We will be attending a industry convention and need a card design that will stand out and be remembered by aircraft owners and private pilots.

Target Market(s)

Aircraft pilots or owners looking for a new upscale hangar

Industry/Entity Type

Airport

Contact Information for Business Card

I like to use very heavy card stock, 400#, double sided. Square, no rounded edges please.

Colors
3276b5
0255a3
85abd2

Requirements
Must have
• An expensive, classy design, vivid colors.
Nice to have
• Needs to look very expensive and classy, and have some "pop". Designer must be able to download or copy my current typeface or fonts.
• One card side might be black with the "Logo and Brindle Sky Port Double line image in blue (or try gold, or glossy black), and perhaps have a grayed out "K720 jet silhouette". The other card side would have our contact info, and perhaps the "BSP Logo only". I'd like my contact info 'stacked', not in a paragraph format.
Should not have
• Should not look "too busy". Having a double-sided card will help.

```html
<!DOCTYPE html>
<html lang="en">
<head>
<meta charset="utf-8">
<title>Brindle Sky Port – Business Card</title>
<link rel="stylesheet" href="https://fonts.googleapis.com/css2?family=Montserrat:wght@400;500;600;800&display=swap">
<style>
  :root {
    --stage: #e9ebee;
    --card-black: #050505;
    --card-white: #ffffff;
    --brand-blue: #0255a3;
    --brand-mid: #3276b5;
    --brand-light: #85abd2;
    --ink: #2a2d33;
    --rule: #3a3d44;
    --sky-top: #ffffff;
    --sky-mid: #f3f4f6;
    --wing-edge: #cfd3d9;
  }
  * { box-sizing: border-box; margin: 0; padding: 0; }
  html, body {
    width: 1200px; height: 900px; overflow: hidden;
    background: var(--stage);
    font-family: "Montserrat", sans-serif;
  }
  .canvas {
    width: 1200px; height: 900px;
    display: flex; flex-direction: column;
    align-items: center; justify-content: center; gap: 40px;
  }
  .card {
    width: 680px; height: 389px;
    border-radius: 0;
    position: relative; overflow: hidden;
    box-shadow: 0 8px 24px rgba(0,0,0,.18);
  }

  /* Front */
  .card--front { background: var(--card-black); display: flex; align-items: center; justify-content: center; }
  .wordmark {
    display: flex; align-items: center; gap: 14px;
    color: #ffffff; font-weight: 800; text-transform: uppercase;
    letter-spacing: 2px; white-space: nowrap;
  }
  .wordmark__square { width: 18px; height: 18px; background: currentColor; flex: none; }
  .card--front .wordmark { font-size: 38px; }

  /* Back */
  .card--back { background: var(--card-white); }
  .aircraft-photo {
    position: absolute; left: 0; top: 0; width: 680px; height: 232px;
    background: linear-gradient(180deg, var(--sky-top) 0%, var(--sky-mid) 55%, var(--wing-edge) 100%);
    clip-path: polygon(0 0, 100% 0, 100% 44%, 50% 100%, 0 44%);
  }
  .wing-line {
    position: absolute; left: 0; top: 0; width: 680px; height: 234px;
    pointer-events: none;
  }
  .wing-line path { fill: none; stroke: var(--wing-edge); stroke-width: 2; }
  .back__logo { position: absolute; left: 40px; bottom: 72px; }
  .card--back .wordmark { color: var(--brand-blue); font-size: 24px; gap: 10px; letter-spacing: 1px; }
  .card--back .wordmark__square { width: 13px; height: 13px; }
  .divider {
    position: absolute; left: 400px; top: 230px; width: 2px; height: 110px;
    background: var(--rule);
  }
  .contact { position: absolute; left: 424px; top: 212px; color: var(--ink); }
  .contact__name { color: var(--brand-mid); font-size: 22px; font-weight: 600; }
  .contact__title { font-size: 13px; margin: 2px 0 10px; }
  .contact__list { list-style: none; font-size: 14px; line-height: 22px; }
  .contact__list li { display: flex; align-items: center; gap: 10px; }
  .contact__list svg { width: 12px; height: 12px; flex: none; fill: none; stroke: var(--brand-blue); stroke-width: 2; }
</style>
</head>
<body>
<main class="canvas">
  <section class="card card--front" aria-label="Card front">
    <div class="wordmark"><span class="wordmark__square"></span>Brindle Sky Port</div>
  </section>

  <section class="card card--back" aria-label="Card back">
    <div class="aircraft-photo" role="img" aria-label="Front view photograph of a private jet in flight against a white sky"></div>
    <svg class="wing-line" viewBox="0 0 680 234" aria-hidden="true"><path d="M0 102 L340 232 L680 102"/></svg>
    <div class="back__logo">
      <div class="wordmark"><span class="wordmark__square"></span>Brindle Sky Port</div>
    </div>
    <div class="divider"></div>
    <div class="contact">
      <p class="contact__name">Marla Quinlan</p>
      <p class="contact__title">Director</p>
      <ul class="contact__list">
        <li><svg viewBox="0 0 12 12"><path d="M2 1.5l2 .2.8 2.4-1.3.9a6 6 0 0 0 3.5 3.5l.9-1.3 2.4.8.2 2c-5 .5-9-3.5-8.5-8.5z"/></svg>+033 2460-5512</li>
        <li><svg viewBox="0 0 12 12"><rect x="1.5" y="4" width="9" height="6" rx="1.5"/><path d="M2 4c1-2.5 7-2.5 8 0"/></svg>+033 2350-7714</li>
        <li><svg viewBox="0 0 12 12"><rect x="1" y="2.5" width="10" height="7"/><path d="M1 2.5l5 4 5-4"/></svg>info@brindleskyport.com</li>
        <li><svg viewBox="0 0 12 12"><circle cx="6" cy="6" r="4.7"/><path d="M1.3 6h9.4M6 1.3c-2.5 3-2.5 6.4 0 9.4M6 1.3c2.5 3 2.5 6.4 0 9.4"/></svg>www.brindleskyport.com</li>
      </ul>
    </div>
  </section>
</main>
</body>
</html>
```